Life Coaching Business - needs business card design with logo

I need a business card and logo design for a life coaching business I started based in Los Angeles. I offer services to clients that wish to bring more balance and overall wholeness to their lives. As of right now, the business name is "Marcus Ellery Coaching." An iidea I had for the logo was to be kind of a Yin-Yang symbol but with dolphins, as the dolphin has symbolic meaning for my business. Although I am really open to other ideas as long as it incorporates the idea of “balance,” “wholeness,” and “dolphins.”I also wanted to incorporate the color blue, maybe in the form of water, waves, or some sort of peaceful imagery.

```html
<!DOCTYPE html>
<html lang="en">
<head>
<meta charset="utf-8">
<title>Marcus Ellery Coaching – Business Card</title>
<link href="https://fonts.googleapis.com/css2?family=Libre+Baskerville:wght@700&family=Lora:wght@400&display=swap" rel="stylesheet">
<style>
  :root {
    --page-bg: #d9d6d1;
    --card-bg: #eef2f5;
    --card-edge: #d3dbe2;
    --navy: #0f2a63;
    --ink: #2a2f38;
    --blue-deep: #0b3f8c;
    --blue-mid: #2f78bd;
    --white: #ffffff;
  }
  * { margin: 0; padding: 0; box-sizing: border-box; }
  html, body { width: 1200px; height: 970px; overflow: hidden; }
  body {
    background: var(--page-bg);
    position: relative;
    font-family: "Lora", Georgia, serif;
  }
  .card {
    position: absolute;
    left: 100px;
    top: 201px;
    width: 1000px;
    height: 568px;
    background: var(--card-bg);
    border: 1px solid var(--card-edge);
    border-radius: 26px;
    overflow: hidden;
    box-shadow: 0 10px 30px rgba(0,0,0,0.12);
  }
  .emblem-panel {
    position: absolute;
    left: 0; top: 0;
    width: 600px; height: 568px;
  }
  .emblem-name {
    position: absolute;
    left: 70px; top: 250px;
    width: 380px;
    text-align: center;
    font-family: "Lora", Georgia, serif;
    font-size: 30px;
    line-height: 1.3;
    color: var(--white);
  }
  .brand {
    position: absolute;
    right: 60px;
    top: 92px;
    width: max-content;
  }
  .brand-name {
    font-family: "Libre Baskerville", Georgia, serif;
    font-weight: 700;
    font-size: 42px;
    color: var(--navy);
    letter-spacing: 0.5px;
    white-space: nowrap;
  }
  .brand-tagline {
    display: flex;
    align-items: center;
    gap: 10px;
    margin-top: 2px;
    font-size: 22px;
    letter-spacing: 6px;
    color: var(--ink);
  }
  .brand-tagline::before,
  .brand-tagline::after {
    content: "";
    flex: 1;
    height: 2px;
    background: var(--ink);
  }
  .address {
    position: absolute;
    right: 60px;
    top: 340px;
    text-align: right;
    font-size: 22px;
    line-height: 30px;
    color: var(--ink);
  }
  .contacts {
    position: absolute;
    right: 50px;
    top: 436px;
    list-style: none;
  }
  .contact-item {
    display: flex;
    justify-content: flex-end;
    align-items: center;
    gap: 12px;
    font-size: 22px;
    line-height: 33px;
    color: var(--ink);
  }
  .contact-icon { width: 28px; height: 28px; flex: none; }
</style>
</head>
<body>
  <div class="card">
    <svg class="emblem-panel" viewBox="0 0 600 568" role="img" aria-label="Brand emblem area in ocean blues">
      <defs>
        <linearGradient id="panelFade" x1="0" y1="0" x2="1" y2="0">
          <stop offset="0" stop-color="#2a6aa8"/>
          <stop offset="0.55" stop-color="#4f8fc6" stop-opacity="0.55"/>
          <stop offset="1" stop-color="#eef2f5" stop-opacity="0"/>
        </linearGradient>
        <linearGradient id="circleFill" x1="0" y1="0" x2="1" y2="1">
          <stop offset="0" stop-color="#2f78bd"/>
          <stop offset="1" stop-color="#0b3f8c"/>
        </linearGradient>
      </defs>
      <rect x="0" y="0" width="600" height="568" fill="url(#panelFade)"/>
      <circle cx="265" cy="290" r="255" fill="url(#circleFill)"/>
    </svg>
    <div class="emblem-name">Marcus Ellery Coaching</div>

    <div class="brand">
      <div class="brand-name">MARCUS ELLERY</div>
      <div class="brand-tagline">COACHING</div>
    </div>

    <div class="address">
      4180 W. Harbor Ln.<br>
      Suite 9, Los Angeles CA
    </div>

    <ul class="contacts">
      <li class="contact-item">310-482-7316
        <svg class="contact-icon" viewBox="0 0 28 28" aria-hidden="true">
          <circle cx="14" cy="14" r="14" fill="var(--navy)"/>
          <path d="M9 10 q0 -2 2 -2 h6 q2 0 2 2 v1 h-3 v-1 h-4 v1 h-3z M8 13 h12 v6 h-12z" fill="var(--white)"/>
          <circle cx="14" cy="16" r="1.8" fill="var(--navy)"/>
        </svg>
      </li>
      <li class="contact-item">hello@elleryinbalance.com
        <svg class="contact-icon" viewBox="0 0 28 28" aria-hidden="true">
          <circle cx="14" cy="14" r="14" fill="var(--navy)"/>
          <rect x="7.5" y="9.5" width="13" height="9" fill="none" stroke="var(--white)" stroke-width="1.6"/>
          <path d="M7.5 9.5 L14 15 L20.5 9.5" fill="none" stroke="var(--white)" stroke-width="1.6"/>
        </svg>
      </li>
      <li class="contact-item">www.elleryinbalance.com
        <svg class="contact-icon" viewBox="0 0 28 28" aria-hidden="true">
          <circle cx="14" cy="14" r="14" fill="var(--navy)"/>
          <circle cx="14" cy="14" r="7" fill="none" stroke="var(--white)" stroke-width="1.4"/>
          <ellipse cx="14" cy="14" rx="3" ry="7" fill="none" stroke="var(--white)" stroke-width="1.2"/>
          <path d="M7 14 h14 M8.5 10.5 h11 M8.5 17.5 h11" stroke="var(--white)" stroke-width="1.1"/>
        </svg>
      </li>
    </ul>
  </div>
</body>
</html>
```